Bright Nook Home Page (A Home Wellness e-commerce site & blog)

We need a dynamic home page created for a home wellness brand. Must be visually appealing and extremely mobile-friendly. Logos and a Navmap have been provided but that is just a guideline, PLEASE USE YOUR CREATIVITY.

Target Market(s)

1st target demo: females 24-48, 2nd target demo: all 24-48

Number of Pages Required

1 page

```html
<!DOCTYPE html>
<html lang="en">
<head>
<meta charset="utf-8">
<title>Bright Nook — Home Wellness</title>
<link href="https://fonts.googleapis.com/css2?family=Lato:wght@400;700&family=Roboto:wght@400;500;700&display=swap" rel="stylesheet">
<style>
:root{
  --ink:#111;
  --text:#222;
  --purple:#4b2190;
  --teal:#2fb3bd;
  --teal-dark:#27a3ad;
  --footer:#2a2a2a;
  --white:#fff;
  --muted:#555;
  --line:#e3e3e3;
}
*{box-sizing:border-box;margin:0;padding:0}
html,body{width:1200px;height:3599px;overflow:hidden}
body{font-family:"Lato",sans-serif;color:var(--text);background:var(--white);position:relative}
.head{font-family:"Roboto",sans-serif}
a{color:inherit;text-decoration:none}

.topbar{height:43px;background:#0d0d0d;color:var(--white);font-size:15px;display:flex;align-items:center;justify-content:center}

.nav{height:72px;background:var(--purple);position:relative;color:var(--white)}
.brand{position:absolute;left:112px;top:14px;font-family:"Lato",sans-serif;font-weight:700;font-size:40px;color:var(--white);display:flex;align-items:center;gap:10px;line-height:1}
.brand .dot{width:20px;height:20px;border-radius:50%;background:var(--teal)}
.social-top{position:absolute;right:120px;top:10px;display:flex;gap:14px;align-items:center}
.soc{width:12px;height:12px;border-radius:50%;background:var(--white);display:block}
.sep{width:1px;height:18px;background:rgba(255,255,255,.7)}
.menu{position:absolute;right:112px;top:42px;display:flex;gap:38px;font-size:16px}
.menu .active{border-bottom:2px solid var(--white);padding-bottom:5px}

.hero{height:593px;position:relative;background:linear-gradient(180deg,#f2f1f3 0%,#eeeaee 45%,#e8c9cf 70%,#d9a4ac 100%);text-align:center}
.hero-photo{position:absolute;left:0;right:0;bottom:0;height:300px;background:linear-gradient(90deg,#e79a96 0%,#edc5cc 25%,#f4d9e3 50%,#e6c1c7 75%,#e58f8a 100%);opacity:.85}
.hero-copy{position:relative;padding-top:75px}
.hero h1{font-size:68px;font-weight:700;color:var(--ink);letter-spacing:1px;line-height:1}
.hero p{font-size:18px;line-height:29px;width:540px;margin:24px auto 0;color:#111}
.btn{display:inline-block;background:var(--teal);color:var(--white);border-radius:26px;font-size:17px}
.hero .btn{margin-top:16px;width:158px;height:49px;line-height:49px}
.arrow{position:absolute;top:390px}
.arrow.l{left:68px}.arrow.r{right:68px}
.dots{position:absolute;bottom:26px;left:50%;transform:translateX(-50%);display:flex;gap:12px}
.dots span{width:11px;height:11px;border-radius:50%;background:rgba(255,255,255,.5)}
.dots span.on{background:var(--white)}

.sale{height:172px;background:var(--teal);color:var(--white);text-align:center;padding-top:40px}
.sale h2{font-size:48px;font-weight:700;line-height:1.1}
.sale p{font-size:27px;font-weight:500}

.bliss{padding-top:73px;height:1088px}
.bliss h2{text-align:center;font-size:35px;font-weight:700;line-height:45px;color:var(--ink)}
.grid{position:absolute;top:1073px;left:116px;width:968px;display:grid;grid-template-columns:317px 316px 316px;grid-template-rows:264px 264px 264px;gap:10px}
.tile{display:block}
.t1{background:linear-gradient(135deg,#c2737c,#8d3a52 55%,#6f5a5a)}
.t2{background:linear-gradient(135deg,#e6dcc8,#e0ad4a 55%,#d6c99a)}
.t3{grid-row:1/3;grid-column:3;background:linear-gradient(160deg,#e8e4e0,#d9b59d 55%,#8c5a45)}
.t4{background:linear-gradient(135deg,#f1efed,#e3dcd3 60%,#d7c190)}
.t5{background:linear-gradient(135deg,#5b6e54,#e2c6d2 50%,#3f4d3b)}
.t6{background:linear-gradient(135deg,#ddd8cf,#b9ad7a 55%,#a49f94)}
.t7{background:linear-gradient(135deg,#efe6d8,#d8ecf2 50%,#6e9a4c)}
.t8{background:linear-gradient(135deg,#5e7b4c,#e7e4de 45%,#6c3a1b)}

.about{height:463px;position:relative;background:linear-gradient(90deg,#eeeeed 0%,#f1f1f0 40%,#ecebea 100%)}
.about-photo{position:absolute;left:480px;top:0;right:0;bottom:0;background:radial-gradient(circle at 30% 20%,#e6b3ae 0,#f0eeec 22%,transparent 40%),radial-gradient(circle at 80% 55%,#f6f6f4 0,#e9eae6 25%,transparent 45%),linear-gradient(135deg,#eeefec,#e5e8e2)}
.about-copy{position:absolute;left:112px;top:96px;width:360px}
.about h2{font-size:35px;font-weight:700;color:var(--ink)}
.about p{font-size:14.5px;line-height:27px;margin-top:16px;color:#333;text-align:justify}
.about .btn{margin-top:22px;width:171px;height:46px;line-height:46px;text-align:center}

.paylater{height:172px;background:var(--teal);color:var(--white);position:relative}
.paylater h2{position:absolute;left:212px;top:38px;font-size:45px;font-weight:700;line-height:48px}
.partner{position:absolute;left:671px;top:46px;display:flex;align-items:center;gap:22px;font-family:"Roboto",sans-serif;font-weight:500;font-size:72px;line-height:1}
.partner .mark{width:76px;height:76px;border-radius:50%;background:var(--white)}

.blog{height:673px;text-align:center;padding-top:80px;position:relative}
.blog h2{font-size:35px;font-weight:700;color:var(--ink)}
.blog .sub{font-size:18px;margin-top:12px;color:#111}
.cards{position:absolute;top:170px;left:112px;display:flex;gap:22px}
.card{width:312px;height:415px;border:1px solid var(--line);text-align:left}
.card .img{height:210px}
.c1{background:linear-gradient(135deg,#4e4036,#b79a84 50%,#6b5444)}
.c2{background:linear-gradient(135deg,#f3efe8,#d9cdbb 50%,#a7917c)}
.c3{background:linear-gradient(135deg,#e8dccb,#c89a7a 50%,#f1ede8)}
.card h3{font-family:"Roboto",sans-serif;font-weight:400;font-size:21px;line-height:28px;margin:16px 16px 0;color:#111}
.card p{font-size:12.5px;line-height:28px;margin:8px 17px 0;color:#333}
.card .more{display:block;margin:4px 17px 0;font-size:13px;font-weight:700;color:var(--teal);text-decoration:underline}

.chat{position:absolute;left:1073px;top:3250px;z-index:2}

.footer{position:absolute;top:3276px;left:0;width:1200px;height:323px;background:var(--footer);color:var(--white)}
.footer .brand{left:112px;top:62px;font-size:38px}
.fsoc{position:absolute;left:140px;top:136px;display:flex;gap:34px}
.fsoc .soc{width:14px;height:14px}
.fcol{position:absolute;top:58px}
.fcol h4{font-family:"Roboto",sans-serif;font-size:16px;font-weight:700;letter-spacing:.3px}
.fcol ul{list-style:none;margin-top:18px}
.fcol li{font-size:14.5px;line-height:30px}
.company{left:396px}.help{left:598px}
.news{left:798px;width:292px}
.news p{font-size:14px;line-height:22px;margin-top:16px}
.signup{margin-top:18px;display:flex;border:1px solid var(--white);height:40px;width:290px}
.signup span{flex:1;background:var(--white);color:#333;font-size:12.5px;line-height:38px;padding-left:12px}
.signup b{width:106px;background:var(--teal);text-align:center;line-height:38px;font-size:16px}
.rule{position:absolute;left:112px;right:112px;top:255px;height:1px;background:#555}
.copy{position:absolute;left:0;right:0;top:276px;text-align:center;font-size:15px}
</style>
</head>
<body>

<div class="topbar">Shipping on all orders $50 and over!"</div>

<header class="nav">
  <a class="brand" href="#"><span class="dot"></span>BrightNook</a>
  <div class="social-top" aria-label="Social links">
    <span class="soc"></span><span class="soc"></span><span class="soc"></span><span class="soc"></span><span class="sep"></span>
    <svg width="22" height="20" viewBox="0 0 22 20" aria-label="Cart"><path d="M1 3h3l2 10h11l2-7H5" fill="none" stroke="#fff" stroke-width="1.4"/><circle cx="8" cy="16.5" r="1.5" fill="#fff"/><circle cx="15" cy="16.5" r="1.5" fill="#fff"/><circle cx="18" cy="3" r="3.2" fill="#fff"/><text x="18" y="4.6" font-size="4.5" text-anchor="middle" fill="#4b2190" font-family="Lato,sans-serif">0</text></svg>
  </div>
  <nav class="menu">
    <a class="active" href="#">Home</a><a href="#">Pages</a><a href="#">Recipe</a><a href="#">Portfolio</a><a href="#">Blog</a><a href="#">Shop</a><a href="#">Contact Us</a>
  </nav>
</header>

<section class="hero">
  <div class="hero-photo" role="img" aria-label="Pink roses beside skincare tubes, bottles and a pot of blush"></div>
  <div class="hero-copy">
    <h1 class="head">BRIGHTNOOK</h1>
    <p>Lorem ipsum dolor sit amet, consectetur adipiscing elit, sed do eiusmod tempor incididunt ut labore et</p>
    <a class="btn" href="#">SHOP NOW</a>
  </div>
  <svg class="arrow l" width="24" height="44" viewBox="0 0 24 44"><path d="M22 1 2 22l20 21" fill="none" stroke="#111" stroke-width="1.6"/></svg>
  <svg class="arrow r" width="24" height="44" viewBox="0 0 24 44"><path d="M2 1l20 21L2 43" fill="none" stroke="#111" stroke-width="1.6"/></svg>
  <div class="dots"><span></span><span class="on"></span><span></span></div>
</section>

<section class="sale head">
  <h2>50% OFF SALE GOING ON NOW!</h2>
  <p>Because saving money also makes us happy</p>
</section>

<section class="bliss">
  <h2 class="head">THE KEY TO TOTAL BLISS IS NURTURING<br>THE MIND,BODY, AND SOUL</h2>
</section>
<div class="grid">
  <div class="tile t1" role="img" aria-label="Orchid flower in a bowl with spa stones"></div>
  <div class="tile t2" role="img" aria-label="Honey, oils, lemon and rosemary with soap bar"></div>
  <div class="tile t3" role="img" aria-label="Facial mask treatment at a spa"></div>
  <div class="tile t4" role="img" aria-label="Rolled towels, candles and orchid"></div>
  <div class="tile t5" role="img" aria-label="Pink water lily on a pond"></div>
  <div class="tile t6" role="img" aria-label="Handmade soap bars tied with twine"></div>
  <div class="tile t7" role="img" aria-label="Candles among green fern leaves"></div>
  <div class="tile t8" role="img" aria-label="Amber pump bottles with a brush and towels"></div>
</div>

<section class="about">
  <div class="about-photo" role="img" aria-label="Pink bath salt, cream jars, white roses and leaves"></div>
  <div class="about-copy">
    <h2 class="head">ABOUT US</h2>
    <p>say that home is where the heart is. But home is also where your mind and body reside. At Bright Nook we believe that home should be your place of Zen. A respite from the crazy world outside those walls. It is where you recharge your soul so you can approach each day with the focus and energy necessary to conquer the world.</p>
    <a class="btn" href="#">TELL ME MORE</a>
  </div>
</section>

<section class="paylater">
  <h2 class="head">DON’T SWEAT IT.<br>YOU CAN PAY LATER.</h2>
  <div class="partner"><span class="mark"></span>Tallyloop</div>
</section>

<section class="blog">
  <h2 class="head">THE HAPPY BLOG</h2>
  <p class="sub">Food forthe mind, tips for the body and exercises for the soul</p>
  <div class="cards">
    <article class="card"><div class="img c1" role="img" aria-label="Bath salt in a wooden bowl with a flower"></div><h3>Sed ut perspiciatis unde oms iste natus error sit volu</h3><p>Lorem ipsum dolor sit amet, nsectetur adipisc-ing elit, sed do eiusmod tempor incididunt ut labore et dolore</p><a class="more" href="#">LEARN MORE&gt;&gt;</a></article>
    <article class="card"><div class="img c2" role="img" aria-label="Rolled towels and a plant in soft light"></div><h3>Sed ut perspiciatis unde oms iste natus error sit volu</h3><p>Lorem ipsum dolor sit amet, nsectetur adipisc-ing elit, sed do eiusmod tempor incididunt ut labore et dolore</p><a class="more" href="#">LEARN MORE&gt;&gt;</a></article>
    <article class="card"><div class="img c3" role="img" aria-label="Couple relaxing at a spa"></div><h3>Sed ut perspiciatis unde oms iste natus error sit volu</h3><p>Lorem ipsum dolor sit amet, nsectetur adipisc-ing elit, sed do eiusmod tempor incididunt ut labore et dolore</p><a class="more" href="#">LEARN MORE&gt;&gt;</a></article>
  </div>
</section>

<svg class="chat" width="56" height="56" viewBox="0 0 56 56" aria-label="Chat"><circle cx="28" cy="28" r="27" fill="#4b2190" stroke="#fff" stroke-width="2"/><path d="M16 27c0-6 5-10 12-10s12 4 12 10-5 10-12 10c-2 0-4 0-5-1l-6 3 2-5c-2-2-3-4-3-7z" fill="#fff"/><circle cx="23" cy="27" r="1.6" fill="#4b2190"/><circle cx="28" cy="27" r="1.6" fill="#4b2190"/><circle cx="33" cy="27" r="1.6" fill="#4b2190"/></svg>

<footer class="footer">
  <a class="brand" href="#"><span class="dot"></span>BrightNook</a>
  <div class="fsoc" aria-label="Social links"><span class="soc"></span><span class="soc"></span><span class="soc"></span><span class="soc"></span></div>
  <div class="fcol company"><h4>COMPANY</h4><ul><li>Our Story</li><li>Careers</li><li>Privacy Policy</li><li>Terms and Conditions</li></ul></div>
  <div class="fcol help"><h4>HELP</h4><ul><li>Returns &amp; Exchanges</li><li>FAQ</li><li>help@brightnook.com</li><li>Size Guide</li><li>Search</li></ul></div>
  <div class="fcol news"><h4>SIGN UP FOR OUR NEWSLETTER</h4><p>Lorem ipsum dolor sit amet, consectetur acing elit, sed do eiusmod te incididunt ut labore et dolore magna aliqua.</p><div class="signup"><span>Enter Your Email</span><b>SUBMIT</b></div></div>
  <div class="rule"></div>
  <p class="copy">© 2021 BrightNook. All Rights Reserved.</p>
</footer>

</body>
</html>
```